Indy Film Production Company/Studio

We need a business card designed from an existing logo. We are a digital studio/production company that caters to creating genre entertainment, like Action, Horror, and martial arts. The card along with the logo will be used to Brand the company from letter heads to banners. The design will also be used for postcards and Brochures. It should be professional and masculine.
Updates

Thank you to all the designers who have participated. I'm narrowing down who it will be. Thank you again.

Target Market(s)

Investors, Networks, Producers, and actors

Industry/Entity Type

Film Production

Contact Information for Business Card

Teodoro Valbuena
Producer/Writer/Director
www.kestrelpicturehouse.example

Requirements
Must have
• Website address, Facebook icon and Twitter icon possibly in the back of the card.
Nice to have
• Logline of Company: Follow The Action.

```html
<!DOCTYPE html>
<html lang="en">
<head>
<meta charset="utf-8">
<title>Kestrel Picture House – Business Card</title>
<link href="https://fonts.googleapis.com/css2?family=Montserrat:ital,wght@1,800&family=Roboto:wght@400;700&display=swap" rel="stylesheet">
<style>
  :root {
    --backdrop: #a8a5a5;
    --card: #f3f3f2;
    --brand-red: #d42e26;
    --ink: #1d1d1d;
    --body-ink: #2e2e2e;
    --band-dark: #262322;
    --divider: #e2e2e2;
    --on-red: #ffffff;
  }
  * { margin: 0; padding: 0; box-sizing: border-box; }
  html, body {
    width: 1200px; height: 1200px; overflow: hidden;
    background: var(--backdrop);
    font-family: "Roboto", Arial, sans-serif;
  }
  .canvas { position: relative; width: 1200px; height: 1200px; }

  .card {
    position: absolute;
    width: 712px; height: 418px;
    background: var(--card);
    overflow: hidden;
  }
  .card--front { left: 238px; top: 119px; }
  .card--back  { left: 230px; top: 643px; }

  .wordmark {
    display: flex; align-items: center; gap: 10px;
    color: var(--brand-red);
    font-family: "Roboto", Arial, sans-serif;
    font-weight: 700;
    letter-spacing: 1px;
    white-space: nowrap;
  }
  .wordmark__square {
    width: 18px; height: 18px; background: var(--brand-red); flex: none;
  }
  .card--front .wordmark {
    position: absolute; left: 0; right: 0; top: 185px;
    justify-content: center; font-size: 34px;
  }
  .card--back .wordmark {
    position: absolute; left: 0; width: 357px; top: 172px;
    justify-content: center; font-size: 21px; letter-spacing: 0.5px;
  }
  .card--back .wordmark__square { width: 13px; height: 13px; }

  .divider {
    position: absolute; left: 357px; top: 60px; width: 1px; height: 300px;
    background: var(--divider);
  }

  .contact { position: absolute; left: 385px; top: 98px; color: var(--body-ink); }
  .contact__name {
    font-family: "Montserrat", Arial, sans-serif;
    font-style: italic; font-weight: 800;
    font-size: 25px; color: var(--ink); line-height: 1.1;
  }
  .contact__role {
    margin-top: 8px; font-size: 16px; color: var(--brand-red);
  }
  .contact__list { list-style: none; margin-top: 30px; font-size: 18px; line-height: 28px; }
  .contact__item { display: flex; align-items: center; gap: 14px; }
  .contact__item svg { width: 20px; height: 16px; flex: none; }
  .contact__address { margin-top: 2px; font-size: 18px; line-height: 28px; }

  .social { display: flex; gap: 10px; margin-top: 14px; }
  .social__dot {
    width: 22px; height: 22px; border-radius: 50%; background: var(--brand-red);
  }

  .band-dark {
    position: absolute; left: 0; bottom: 0; width: 360px; height: 27px;
    background: var(--band-dark);
  }
  .band-red {
    position: absolute; right: 0; bottom: 0; width: 400px; height: 52px;
  }
  .band-red svg { display: block; }
  .band-red__url {
    position: absolute; left: 385px; bottom: 16px;
    font-size: 17px; color: var(--on-red); white-space: nowrap;
  }
</style>
</head>
<body>
<main class="canvas">

  <section class="card card--front" aria-label="Card front">
    <div class="wordmark"><span class="wordmark__square"></span>KESTREL PICTURE HOUSE</div>
  </section>

  <section class="card card--back" aria-label="Card back">
    <div class="wordmark"><span class="wordmark__square"></span>KESTREL PICTURE HOUSE</div>
    <div class="divider"></div>

    <div class="contact">
      <h1 class="contact__name">Teodoro Valbuena</h1>
      <p class="contact__role">Producer/Writer/Director</p>
      <ul class="contact__list">
        <li class="contact__item">
          <svg viewBox="0 0 20 16" aria-hidden="true">
            <path d="M2 5 Q10 0 18 5 L16 7 L13 5.5 L13 4 Q10 3 7 4 L7 5.5 L4 7 Z" fill="var(--brand-red)"/>
            <path d="M5 8 L15 8 L17 15 L3 15 Z" fill="var(--brand-red)"/>
            <circle cx="10" cy="11.5" r="1.8" fill="var(--card)"/>
          </svg>
          <span>+00 111 222 3333</span>
        </li>
        <li class="contact__item">
          <svg viewBox="0 0 20 16" aria-hidden="true">
            <rect x="1" y="2" width="18" height="12" fill="var(--brand-red)"/>
            <path d="M1 2 L10 9 L19 2" fill="none" stroke="var(--card)" stroke-width="1.5"/>
          </svg>
          <span>team@kestrelph.example</span>
        </li>
      </ul>
      <p class="contact__address">Your Long Commercial or<br>business address in 2 line</p>
      <div class="social" aria-label="Social media links">
        <span class="social__dot" role="img" aria-label="Social network one"></span>
        <span class="social__dot" role="img" aria-label="Social network two"></span>
      </div>
    </div>

    <div class="band-dark"></div>
    <div class="band-red">
      <svg width="400" height="52" viewBox="0 0 400 52" aria-hidden="true">
        <polygon points="28,0 400,0 400,52 0,52" fill="var(--brand-red)"/>
      </svg>
    </div>
    <p class="band-red__url">www.kestrelpicturehouse.example</p>
  </section>

</main>
</body>
</html>
```